Marlow Vale Stud website

We would like to create a horse stud/agistment farm website similar to this websites we have attached below:
www.thornbeck.com.au
www.quillstead.com.au
www.brackley.com
www.pimsey.com.au
The main colour scheme are purple and white to align with the stable's racing colours.
We have also attach the company logo and also images of the farm and create some ideas for the website.
Many thanks for looking into this project!

```html
<!DOCTYPE html>
<html lang="en">
<head>
<meta charset="utf-8">
<title>Marlow Vale Stud</title>
<link href="https://fonts.googleapis.com/css2?family=Crimson+Text:wght@600;700&family=Open+Sans:wght@400;600&display=swap" rel="stylesheet">
<style>
:root{
  --purple:#4a1d57;
  --purple-deep:#3c1347;
  --ink:#2b2b2b;
  --muted:#8a8a8a;
  --light:#f3f3f3;
  --white:#ffffff;
  --grass:#5f7d3a;
  --grass-light:#88a35a;
  --sky:#b9c7b0;
  --bay:#7a4326;
}
*{box-sizing:border-box;margin:0;padding:0}
html,body{width:1200px;height:3688px;overflow:hidden}
body{position:relative;font-family:"Open Sans",Arial,sans-serif;color:var(--ink);background:var(--white)}
.serif{font-family:"Crimson Text",Georgia,serif}
.photo{position:absolute}

/* hero */
.hero{position:absolute;left:0;top:0;width:1200px;height:660px;
  background:linear-gradient(180deg,#3f4f2c 0%,#55682f 35%,#6c8a3c 70%,#7f9c49 100%)}
.nav{position:absolute;left:72px;top:32px;width:1056px;height:100px;background:var(--white);
  display:flex;align-items:center;justify-content:space-between;padding:0 24px 0 28px}
.brand{display:flex;align-items:center;gap:12px;font-family:"Crimson Text",Georgia,serif;font-weight:700;font-size:22px;color:var(--purple)}
.brand-dot{width:40px;height:40px;border-radius:50%;background:var(--purple)}
.nav ul{list-style:none;display:flex;gap:26px}
.nav li{font-size:13px;letter-spacing:.5px;color:#666}
.nav li.active{color:var(--ink);font-weight:600}
.hero h1{position:absolute;left:0;top:300px;width:1200px;text-align:center;color:var(--white);
  font-family:"Crimson Text",Georgia,serif;font-weight:600;font-size:64px;line-height:74px;letter-spacing:1px}
.thumbs{position:absolute;top:604px;left:0;width:1200px;display:flex;justify-content:center;gap:28px}
.thumb{width:112px;height:112px;border-radius:50%;border:5px solid var(--white);
  background:radial-gradient(circle at 50% 60%,var(--bay),var(--grass) 70%)}

/* section headings */
.section-title{position:absolute;left:0;width:1200px;text-align:center;color:var(--purple);
  font-family:"Crimson Text",Georgia,serif;font-weight:700;font-size:46px}

/* stallions */
.stallion{position:absolute;top:888px;height:184px;background:var(--white)}
.stallion .pic{height:136px;background:linear-gradient(180deg,#7f9a5a,#5a7a35)}
.stallion .name{height:48px;background:var(--purple);color:var(--white);font-size:13px;padding:15px 12px}
.stallion.featured{top:860px;height:240px;box-shadow:0 10px 24px rgba(0,0,0,.3)}
.stallion.featured .pic{height:184px;background:linear-gradient(180deg,#9aa9a0,#6f8a55)}
.stallion.featured .name{height:56px;padding:19px 16px}
.dots{position:absolute;top:1170px;left:530px;display:flex;gap:10px}
.dots span{width:40px;height:5px;background:#ddd}
.dots span.on{background:#999}

/* about */
.about-frame{position:absolute;left:88px;top:1272px;width:420px;height:360px;border:10px solid var(--purple);border-right:none;border-bottom:none}
.about-photo{left:100px;top:1290px;width:456px;height:330px;background:linear-gradient(180deg,#466b2a 0%,#6c8e3a 50%,#8cad4d 100%)}
.about-text{position:absolute;left:656px;top:1300px;width:430px}
.about-text h2{font-family:"Crimson Text",Georgia,serif;font-weight:700;font-size:46px;color:var(--purple);margin-bottom:14px}
.about-text p{font-size:13px;line-height:22px;color:var(--muted);margin-bottom:16px}
.btn{display:inline-block;margin-top:8px;border:2px solid var(--ink);padding:12px 36px;font-family:"Crimson Text",Georgia,serif;font-weight:700;font-size:16px;letter-spacing:1px}

/* wide band */
.band-photo{left:0;top:1720px;width:1200px;height:452px;background:linear-gradient(180deg,#4c6a33 0%,#6b8441 45%,#8aa457 100%)}

/* gallery */
.gallery-title{position:absolute;left:80px;top:2284px;font-family:"Crimson Text",Georgia,serif;font-weight:700;font-size:46px;color:var(--purple)}
.g1{left:80px;top:2372px;width:248px;height:176px;background:linear-gradient(180deg,#9bb3c8,#5f7d3a)}
.g2{left:348px;top:2372px;width:248px;height:176px;background:linear-gradient(180deg,#c7cfc9,#6f9343)}
.g3{left:80px;top:2572px;width:516px;height:180px;background:linear-gradient(180deg,#a9b7a3,#5e7a39)}
.g4{left:620px;top:2272px;width:500px;height:480px;background:linear-gradient(180deg,#6a4a2f 0%,#3e5a2a 40%,#6f8f3e 100%)}

/* news */
.news{position:absolute;left:0;top:2840px;width:1200px;height:580px;background:var(--light)}
.news-item{position:absolute;top:120px;width:320px}
.news-item .pic{height:208px;background:linear-gradient(180deg,#7d9566,#4f6d30)}
.news-item h3{font-size:16px;font-weight:600;line-height:22px;margin:22px 0 12px;color:var(--ink)}
.news-item p{font-size:12px;line-height:19px;color:var(--muted)}

/* footer */
.footer{position:absolute;left:0;top:3420px;width:1200px;height:268px;background:var(--purple-deep);color:var(--white);text-align:center}
.social{position:absolute;top:62px;left:0;width:1200px;display:flex;justify-content:center;gap:30px}
.social span{width:40px;height:40px;border-radius:50%;border:2px solid rgba(255,255,255,.7)}
.foot-links{position:absolute;top:150px;left:0;width:1200px;display:flex;justify-content:center;gap:40px;list-style:none;font-size:13px}
.copy{position:absolute;top:204px;left:0;width:1200px;font-size:11px;color:rgba(255,255,255,.7)}
</style>
</head>
<body>

<header class="hero" role="img" aria-label="Photo of a herd of horses galloping across a green paddock">
  <nav class="nav">
    <div class="brand"><span class="brand-dot"></span>Marlow Vale Stud</div>
    <ul>
      <li class="active">HOME</li><li>STALLIONS</li><li>NEWS</li><li>SALES</li><li>GALLERY</li><li>ABOUT</li><li>CONTACT</li>
    </ul>
  </nav>
  <h1>Inter relation Between<br>Horse &amp; Rider</h1>
  <div class="thumbs">
    <div class="thumb" role="img" aria-label="Thumbnail of horses in a paddock"></div>
    <div class="thumb" role="img" aria-label="Thumbnail of a rider on a horse"></div>
    <div class="thumb" role="img" aria-label="Thumbnail of a chestnut horse"></div>
  </div>
</header>

<h2 class="section-title" style="top:784px">Stallions</h2>
<div class="stallion" style="left:0;width:220px"><div class="pic" role="img" aria-label="Photo of a bay stallion"></div><div class="name">Keeper Of The Vale</div></div>
<div class="stallion" style="left:240px;width:232px"><div class="pic" role="img" aria-label="Photo of a dark bay stallion"></div><div class="name">Silver Lantern</div></div>
<div class="stallion featured" style="left:480px;width:240px"><div class="pic" role="img" aria-label="Photo of a chestnut stallion"></div><div class="name">Harbour Bloom</div></div>
<div class="stallion" style="left:732px;width:228px"><div class="pic" role="img" aria-label="Photo of a bay stallion"></div><div class="name">Keeper Of The Vale</div></div>
<div class="stallion" style="left:972px;width:228px"><div class="pic" role="img" aria-label="Photo of a chestnut stallion"></div><div class="name">North Quill</div></div>
<div class="dots"><span class="on"></span><span></span><span></span></div>

<div class="about-frame"></div>
<div class="photo about-photo" role="img" aria-label="Photo of a bay horse trotting in a green paddock"></div>
<section class="about-text">
  <h2>About us</h2>
  <p>Marlow Vale has bred and raised quality thoroughbreds on rolling green pasture for three generations, offering careful agistment, foaling and spelling services to owners who want their horses handled with patience, skill and genuine care every single day.</p>
  <p>Our team rides, feeds and watches every horse, keeping each one fit, settled and ready for its next step.</p>
  <span class="btn">KNOW MORE</span>
</section>

<div class="photo band-photo" role="img" aria-label="Photo of two chestnut horses playing in a fenced paddock"></div>

<h2 class="gallery-title">Our Gallery</h2>
<div class="photo g1" role="img" aria-label="Photo of horses standing in a row"></div>
<div class="photo g2" role="img" aria-label="Photo of a grey horse grazing"></div>
<div class="photo g3" role="img" aria-label="Aerial photo of the stud farm buildings"></div>
<div class="photo g4" role="img" aria-label="Photo of a jockey in purple silks riding a grey horse"></div>

<section class="news">
  <h2 class="section-title" style="top:56px">Latest News</h2>
  <article class="news-item" style="left:80px">
    <div class="pic" role="img" aria-label="Photo of handlers leading horses down a lane"></div>
    <h3>Spring foals settle in well across the northern paddocks this season</h3>
    <p>The first foals of the year are growing strong and curious, and our staff report a calm, healthy start for every mare.</p>
  </article>
  <article class="news-item" style="left:440px">
    <div class="pic" role="img" aria-label="Photo of a handler with horses in a yard"></div>
    <h3>New agistment yards open beside the river flats this month</h3>
    <p>Fresh fencing, shade shelters and clean water points now give visiting horses more room to rest between their racing campaigns.</p>
  </article>
  <article class="news-item" style="left:800px">
    <div class="pic" role="img" aria-label="Photo of a jockey riding a horse at the track"></div>
    <h3>Homebred runner wins in purple colours at the autumn meeting</h3>
    <p>A proud day for the farm as one of our own crossed the line first, ridden hard and clean to the very end.</p>
  </article>
</section>

<footer class="footer">
  <div class="social"><span></span><span></span><span></span><span></span></div>
  <ul class="foot-links"><li>Home</li><li>Stallions</li><li>News</li><li>Sales</li><li>Gallery</li><li>About</li><li>Contact</li></ul>
  <p class="copy">2016 Marlow Vale Stud - All Rights Reserved</p>
</footer>

</body>
</html>
```